Corvane Holdings , new business card design

investment firm with corporate clients . need double sided business card , vertical and horizontal options ,logo must be clear. prefer pantone colors only and sharp design. website also www.corvane.ae

Khalid Bin Tarrafi
Managing Director
Tel. +971 4 387 2940
Mobile +971 50 518 2403
khalid@corvane.ae
Q-Span Plaza, officw 18-B07, Warqa Gardens, Dubai

Contact Information for Business Card

Khalid Bin Tarrafi
Managing Director

Font styles to use
Serif

Colors

Designer to choose colors to be used in the design.

```html
<!DOCTYPE html>
<html lang="en">
<head>
<meta charset="utf-8">
<title>Corvane Holdings — Business Card</title>
<link href="https://fonts.googleapis.com/css2?family=Lato:wght@300;400&display=swap" rel="stylesheet">
<style>
  :root {
    --page: #e9e9ea;
    --card-white: #f7f7f8;
    --card-blue: #426f96;
    --ink: #1b1f29;
    --accent: #3f6a93;
    --paper: #ffffff;
    --faint: #8da6c0;
  }
  * { margin: 0; padding: 0; box-sizing: border-box; }
  html, body { width: 1200px; height: 1200px; overflow: hidden; }
  body {
    background: var(--page);
    font-family: "Lato", sans-serif;
    position: relative;
  }
  .card {
    position: absolute;
    left: 180px;
    width: 840px;
    height: 480px;
    box-shadow: 0 6px 18px rgba(0,0,0,0.12);
  }
  .card--front { top: 80px; background: var(--card-white); }
  .card--back { top: 640px; background: var(--card-blue); color: var(--paper); }

  .brand {
    position: absolute;
    display: flex;
    align-items: center;
    gap: 18px;
    font-weight: 300;
    text-transform: uppercase;
    white-space: nowrap;
  }
  .brand__mark { display: block; }
  .card--front .brand {
    left: 50%; top: 50%;
    transform: translate(-50%, -50%);
    font-size: 44px;
    letter-spacing: 12px;
    color: var(--ink);
  }
  .card--front .brand__mark { width: 22px; height: 22px; background: var(--accent); }
  .card--back .brand {
    left: 70px; top: 44px;
    font-size: 30px;
    letter-spacing: 9px;
    color: var(--faint);
  }
  .card--back .brand__mark { width: 16px; height: 16px; background: var(--faint); }

  .holder { position: absolute; left: 70px; top: 112px; }
  .holder__name { font-size: 40px; font-weight: 400; letter-spacing: 0.5px; }
  .holder__title { font-size: 24px; font-weight: 300; margin-top: 2px; }
  .rule { position: absolute; left: 70px; top: 214px; width: 700px; height: 2px; background: var(--paper); }

  .contact {
    position: absolute; left: 70px; top: 250px;
    display: grid;
    grid-template-columns: 100px 22px auto;
    row-gap: 6px;
    font-size: 26px;
    font-weight: 300;
  }
  .contact dd { font-weight: 400; }

  .address {
    position: absolute; right: 70px; top: 250px;
    text-align: right; font-size: 22px; font-weight: 300; line-height: 1.4;
    font-style: normal;
  }
  .website {
    position: absolute; right: 70px; bottom: 44px;
    font-size: 26px; font-weight: 400;
  }
</style>
</head>
<body>
  <section class="card card--front" aria-label="Card front">
    <div class="brand"><span class="brand__mark"></span>Corvane Holdings</div>
  </section>

  <section class="card card--back" aria-label="Card back">
    <div class="brand"><span class="brand__mark"></span>Corvane Holdings</div>
    <div class="holder">
      <h1 class="holder__name">Khalid Bin Tarrafi</h1>
      <p class="holder__title">Managing Director</p>
    </div>
    <div class="rule"></div>
    <dl class="contact">
      <dt>Tel</dt><span>:</span><dd>+971 4 387 2940</dd>
      <dt>Mobile</dt><span>:</span><dd>+971 50 518 2403</dd>
      <dt>Email</dt><span>:</span><dd>khalid@corvane.ae</dd>
    </dl>
    <address class="address">Q-Span Plaza, officw 18-B07,<br>Warqa Gardens, Dubai</address>
    <p class="website">www.corvane.ae</p>
  </section>
</body>
</html>
```